Dental Medical History Form - Content provided

Design a medical history form for a dental practice. Content is provided so all that is needed is the formatting to make it look great and easy to read.

"Patient Information" to include all information contained in top portion of the "Patient Medical History Form" docx file.

"Medical History" should follow the formatting and content of the "Exact Medical History" file as this is what the entry fields look like in our practice software and so we would like it to match.

1st page - Patient info, allergies, medications, antibiotics, joint replacement, pregnancy.

2nd page - Do you have, or have you had, any of the following? . . . . . . .
Updates

Target Market(s)

All ages but must be clear enough for elderly to read. Use as much space as possible to keep font size bigger yet keep to two pages

Industry/Entity Type

Dental

Font styles to use
Sans Serif

Requirements
Must have
• All content provided
• Our logo at the top (file provided)
• Century Gothic Font
• Limit to two pages

```html
<!DOCTYPE html>
<html lang="en">
<head>
<meta charset="utf-8">
<title>Harbour Dental – Confidential Medical History</title>
<link href="https://fonts.googleapis.com/css2?family=Didact+Gothic&family=Montserrat:wght@700;800&display=swap" rel="stylesheet">
<style>
:root{
  --backdrop:#5b534c;
  --paper:#ffffff;
  --ink:#2e2e2e;
  --muted:#6a6a6a;
  --band-dark:#4b4e53;
  --band-light:#d6d6d6;
  --head-fill:#e4e4e4;
  --rule:#555555;
}
*{box-sizing:border-box;margin:0;padding:0}
html,body{width:1200px;height:900px;overflow:hidden}
body{background:var(--backdrop);font-family:"Didact Gothic",sans-serif;color:var(--ink);position:relative}
.sheet{position:absolute;top:64px;width:550px;height:772px;background:var(--paper);overflow:hidden;font-size:9.6px}
.sheet--info{left:42px}
.sheet--history{left:614px}
.top-band{position:absolute;left:0;top:0;width:100%;height:15px;background:var(--band-dark)}
.top-band::before{content:"";position:absolute;left:0;top:0;height:15px;width:175px;background:var(--band-light);clip-path:polygon(0 0,100% 0,calc(100% - 12px) 100%,0 100%)}
.sheet--history .top-band::before{width:170px}
.abs{position:absolute}
.brand{position:absolute;font-family:"Didact Gothic",sans-serif;color:var(--muted);font-size:27px;letter-spacing:-.3px;line-height:1}
.title-bar{position:absolute;left:218px;top:36px;width:304px;height:22px;display:flex;align-items:stretch}
.title-bar::before{content:"";width:40px;flex:none;background:repeating-linear-gradient(120deg,var(--band-light) 0 3px,transparent 3px 7px)}
.title-bar span{flex:1;background:var(--band-dark);color:#fff;font-family:"Montserrat",sans-serif;font-weight:800;font-size:12.5px;letter-spacing:.1px;display:flex;align-items:center;justify-content:flex-end;padding-right:8px;white-space:nowrap}

.sec-head{position:absolute;height:15px;display:flex;align-items:stretch;white-space:nowrap;font-family:"Montserrat",sans-serif;font-weight:700;font-size:8.8px;letter-spacing:-.05px}
.sec-head span{display:flex;align-items:center;background:var(--head-fill);padding:0 8px 0 1px}
.sec-head::after{content:"";width:30px;flex:none;background:repeating-linear-gradient(120deg,var(--head-fill) 0 3px,transparent 3px 7px)}

.field{position:absolute;display:flex;align-items:flex-end;height:13px;white-space:nowrap}
.field .line{flex:1;border-bottom:.8px solid var(--rule);margin-left:3px;height:9px;position:relative}
.sub{position:absolute;top:10px;font-size:5.5px;color:var(--muted)}
.box{display:inline-block;width:7px;height:7px;border:.9px solid var(--ink);margin-right:4px;vertical-align:-0.5px}
.opt{position:absolute;white-space:nowrap}
.yn{position:absolute;white-space:nowrap}
.yn b{font-weight:400;margin-right:9px}
.checklist{position:absolute;list-style:none}
.checklist li{height:13px;line-height:13px;position:relative;white-space:nowrap}
.checklist .yn{top:0}
.thanks{position:absolute;left:228px;top:697px;width:300px;font-style:italic;font-size:7.2px;line-height:11px}
.foot{position:absolute;left:0;top:732px;width:550px;height:16px;background:var(--band-dark);color:#fff;font-size:11px;display:flex;align-items:center;white-space:nowrap}
.foot-phone{position:relative;width:176px;height:16px;background:var(--band-light);color:var(--ink);font-family:"Montserrat",sans-serif;font-weight:700;font-size:11px;display:flex;align-items:center;padding-left:38px;gap:6px;clip-path:polygon(0 0,100% 0,calc(100% - 9px) 100%,0 100%)}
.foot-addr{display:flex;align-items:center;gap:5px;padding-left:8px}
.foot svg{flex:none}
</style>
</head>
<body>

<section class="sheet sheet--info">
  <div class="top-band"></div>
  <div class="brand" style="left:28px;top:34px">harbour dental</div>
  <div class="title-bar"><span>CONFIDENTIAL MEDICAL HISTORY</span></div>

  <div class="sec-head" style="left:27px;top:96px"><span>PERSONAL INFORMATION</span></div>
  <div class="field" style="left:28px;top:126px;width:228px">Name :<span class="line"><span class="sub" style="left:18px">First</span><span class="sub" style="left:90px">Middle</span><span class="sub" style="left:160px">Last</span></span></div>
  <div class="field" style="left:28px;top:151px;width:228px">Address :<span class="line"></span></div>
  <div class="field" style="left:28px;top:176px;width:228px">DOB :<span class="line"></span></div>
  <div class="field" style="left:28px;top:201px;width:228px">Email Address :<span class="line"></span></div>
  <div class="field" style="left:28px;top:226px;width:228px">Phone Number(s) :<span class="line"><span class="sub" style="left:14px">Mobile</span><span class="sub" style="left:64px">Work</span><span class="sub" style="left:108px">Home</span></span></div>

  <div class="sec-head" style="left:27px;top:262px"><span>EMERGENCY CONTACT PERSON</span></div>
  <div class="field" style="left:28px;top:291px;width:228px">Name :<span class="line"></span></div>
  <div class="field" style="left:28px;top:316px;width:228px">Relationship :<span class="line"></span></div>
  <div class="field" style="left:28px;top:341px;width:228px">Phone Number :<span class="line"></span></div>

  <div class="sec-head" style="left:290px;top:96px"><span>GENERAL PRACTITIONER</span></div>
  <div class="field" style="left:291px;top:126px;width:231px">Name :<span class="line"></span></div>
  <div class="field" style="left:291px;top:151px;width:231px">Practice Name :<span class="line"></span></div>
  <div class="field" style="left:291px;top:176px;width:231px">Phone Number :<span class="line"></span></div>
  <div class="abs" style="left:291px;top:202px;line-height:12.5px">Do you have a health fund with<br>dental cover?</div>
  <div class="yn" style="left:446px;top:214px"><span class="box"></span><b>Yes</b><span class="box"></span>No</div>
  <div class="abs" style="left:291px;top:239px">If so, what is the name of the fund?</div>
  <div class="abs" style="left:291px;top:264px">Fund Number?</div>
  <div class="abs" style="left:291px;top:288px">Priority Number of card :&nbsp; 0&nbsp; 1&nbsp; 2&nbsp; 3&nbsp; 4&nbsp; 5</div>

  <div class="sec-head" style="left:27px;top:371px"><span>PLEASE INDICATE IF YOU ARE ALLERGIC TO ANY OF THE FOLLOWING &#9745;?</span></div>
  <div class="opt" style="left:28px;top:398px"><span class="box"></span> Aspirin</div>
  <div class="opt" style="left:28px;top:414px"><span class="box"></span> Codeine</div>
  <div class="opt" style="left:28px;top:430px"><span class="box"></span> Penicillin</div>
  <div class="opt" style="left:110px;top:398px"><span class="box"></span> Sulfites</div>
  <div class="opt" style="left:110px;top:414px"><span class="box"></span> Latex</div>
  <div class="opt" style="left:110px;top:430px"><span class="box"></span> Local Anaesthetic</div>
  <div class="opt" style="left:230px;top:398px"><span class="box"></span> Nickel</div>
  <div class="field" style="left:230px;top:414px;width:292px"><span class="box"></span> Other:<span class="line"></span></div>

  <div class="sec-head" style="left:27px;top:460px;font-size:8.5px"><span>ARE YOU CURRENTLY TAKING, OR HAVE EVER TAKEN, ANY OF THE FOLLOWING MEDICATION &#9745;?</span></div>
  <div class="opt" style="left:28px;top:486px"><span class="box"></span> Asthma inhaler</div>
  <div class="opt" style="left:28px;top:502px"><span class="box"></span> Anti-epileptics</div>
  <div class="opt" style="left:28px;top:519px"><span class="box"></span> Anti-depressants</div>
  <div class="opt" style="left:28px;top:535px"><span class="box"></span> Blood Pressure</div>
  <div class="opt" style="left:142px;top:486px"><span class="box"></span> Blood Thinners</div>
  <div class="opt" style="left:142px;top:502px"><span class="box"></span> Bisphosphonates</div>
  <div class="opt" style="left:142px;top:519px"><span class="box"></span> Chemotherapy</div>
  <div class="opt" style="left:142px;top:535px"><span class="box"></span> Insulin</div>
  <div class="opt" style="left:261px;top:486px"><span class="box"></span> Immunosuppressants</div>
  <div class="opt" style="left:261px;top:502px"><span class="box"></span> Steroids</div>
  <div class="opt" style="left:261px;top:519px"><span class="box"></span> Oral Contraceptive</div>
  <div class="field" style="left:261px;top:533px;width:261px"><span class="box"></span> Other:<span class="line"></span></div>

  <div class="sec-head" style="left:27px;top:565px"><span>PLEASE SPECIFY MEDICATION NAME, DOES, AND FREQUENCY WHERE POSSIBLE</span></div>
  <div class="abs" style="left:28px;top:599px;width:494px;border-bottom:.8px solid var(--rule)"></div>
  <div class="abs" style="left:28px;top:621px;width:494px;border-bottom:.8px solid var(--rule)"></div>
  <div class="abs" style="left:28px;top:643px;width:494px;border-bottom:.8px solid var(--rule)"></div>

  <div class="abs" style="left:28px;top:660px">Do you require antibiotic cover? <span class="box" style="margin-left:2px"></span>Yes&nbsp;&nbsp;<span class="box"></span>No</div>
  <div class="abs" style="left:262px;top:660px">Have you had a joint replacement ? <span class="box" style="margin-left:2px"></span>Yes&nbsp;&nbsp;&nbsp;<span class="box"></span>No</div>

  <div class="sec-head" style="left:27px;top:683px"><span>FOR WOMEN</span></div>
  <div class="abs" style="left:28px;top:703px">Are you Pregnant?&nbsp;&nbsp;&nbsp;<span class="box"></span>Yes&nbsp;&nbsp;<span class="box"></span>No&nbsp;&nbsp;<span class="box"></span>Possible</div>
  <div class="abs" style="left:263px;top:703px">Breast Feeding?&nbsp;&nbsp;<span class="box"></span>Yes&nbsp;&nbsp;<span class="box"></span>No</div>

  <footer class="foot">
    <div class="foot-phone"><svg width="10" height="10" viewBox="0 0 20 20"><circle cx="10" cy="10" r="8.6" fill="none" stroke="currentColor" stroke-width="1.6"/><path d="M7 5.5l1.6 2.4-1 1.2a6 6 0 0 0 3.3 3.3l1.2-1 2.4 1.6-.8 1.6c-3.8-.3-7.2-3.7-7.5-7.5z" fill="currentColor"/></svg>(02) 40 123 456</div>
    <div class="foot-addr"><svg width="7" height="10" viewBox="0 0 14 20"><path d="M7 0a7 7 0 0 0-7 7c0 5 7 13 7 13s7-8 7-13a7 7 0 0 0-7-7zm0 9.5A2.5 2.5 0 1 1 7 4.5a2.5 2.5 0 0 1 0 5z" fill="currentColor"/></svg>Harbour Dental, 3.04/118 Coastline Rd, Bayview NSW. 2260</div>
  </footer>
</section>

<section class="sheet sheet--history">
  <div class="top-band"></div>
  <div class="sec-head" style="left:27px;top:30px"><span>DO YOU HAVE, OR HAVE YOU HAD, ANY OF THE FOLLOWING?</span></div>

  <div class="sec-head" style="left:27px;top:51px"><span>DENTAL</span></div>
  <ul class="checklist" style="left:28px;top:71px;width:250px">
    <li>Acid Reflux<span class="yn" style="left:178px"><span class="box"></span><b>Yes</b><span class="box"></span>No</span></li>
    <li>Bad Breath/Taste<span class="yn" style="left:178px"><span class="box"></span><b>Yes</b><span class="box"></span>No</span></li>
    <li>Bleeding/Swollen/Sore Gums<span class="yn" style="left:178px"><span class="box"></span><b>Yes</b><span class="box"></span>No</span></li>
    <li>Blisters/Ulcers in Mouth<span class="yn" style="left:178px"><span class="box"></span><b>Yes</b><span class="box"></span>No</span></li>
    <li>Broken tooth/filling<span class="yn" style="left:178px"><span class="box"></span><b>Yes</b><span class="box"></span>No</span></li>
    <li>Burning tongue<span class="yn" style="left:178px"><span class="box"></span><b>Yes</b><span class="box"></span>No</span></li>
    <li>Dry mouth<span class="yn" style="left:178px"><span class="box"></span><b>Yes</b><span class="box"></span>No</span></li>
    <li>Food collection between teeth<span class="yn" style="left:178px"><span class="box"></span><b>Yes</b><span class="box"></span>No</span></li>
    <li>Grinding/Clenching teeth (day/night)<span class="yn" style="left:178px"><span class="box"></span><b>Yes</b><span class="box"></span>No</span></li>
    <li>loose teeth<span class="yn" style="left:178px"><span class="box"></span><b>Yes</b><span class="box"></span>No</span></li>
    <li>Crooked teeth<span class="yn" style="left:178px"><span class="box"></span><b>Yes</b><span class="box"></span>No</span></li>
    <li>Discoloured teeth<span class="yn" style="left:178px"><span class="box"></span><b>Yes</b><span class="box"></span>No</span></li>
    <li>Sensitivity to Hot/Cold<span class="yn" style="left:178px"><span class="box"></span><b>Yes</b><span class="box"></span>No</span></li>
    <li>Tooth pain when chewing<span class="yn" style="left:178px"><span class="box"></span><b>Yes</b><span class="box"></span>No</span></li>
    <li>Jaw Pain/Fracture<span class="yn" style="left:178px"><span class="box"></span><b>Yes</b><span class="box"></span>No</span></li>
    <li>orthodontic treatment/history<span class="yn" style="left:178px"><span class="box"></span><b>Yes</b><span class="box"></span>No</span></li>
    <li>Oral Cancer<span class="yn" style="left:178px"><span class="box"></span><b>Yes</b><span class="box"></span>No</span></li>
  </ul>

  <div class="sec-head" style="left:27px;top:303px"><span>DIET / LIFESTYLE</span></div>
  <ul class="checklist" style="left:28px;top:323px;width:250px">
    <li style="font-size:8.4px">Drink more than one glass alchohol per day<span class="yn" style="left:178px;font-size:9.6px"><span class="box"></span><b>Yes</b><span class="box"></span>No</span></li>
    <li>Smoking<span class="yn" style="left:178px"><span class="box"></span><b>Yes</b><span class="box"></span>No</span></li>
    <li>Carbonated drinks<span class="yn" style="left:178px"><span class="box"></span><b>Yes</b><span class="box"></span>No</span></li>
    <li>Sugary foods<span class="yn" style="left:178px"><span class="box"></span><b>Yes</b><span class="box"></span>No</span></li>
  </ul>

  <div class="sec-head" style="left:27px;top:387px"><span>BLOOD</span></div>
  <ul class="checklist" style="left:28px;top:407px;width:250px">
    <li>Anaemia<span class="yn" style="left:178px"><span class="box"></span><b>Yes</b><span class="box"></span>No</span></li>
    <li>Blood clots<span class="yn" style="left:178px"><span class="box"></span><b>Yes</b><span class="box"></span>No</span></li>
    <li>Leukemia<span class="yn" style="left:178px"><span class="box"></span><b>Yes</b><span class="box"></span>No</span></li>
    <li>Low platelets<span class="yn" style="left:178px"><span class="box"></span><b>Yes</b><span class="box"></span>No</span></li>
    <li>Lymphoma<span class="yn" style="left:178px"><span class="box"></span><b>Yes</b><span class="box"></span>No</span></li>
    <li>Haemophelia<span class="yn" style="left:178px"><span class="box"></span><b>Yes</b><span class="box"></span>No</span></li>
  </ul>

  <div class="sec-head" style="left:27px;top:496px"><span>CHEST</span></div>
  <ul class="checklist" style="left:28px;top:516px;width:250px">
    <li>Bronchitis<span class="yn" style="left:178px"><span class="box"></span><b>Yes</b><span class="box"></span>No</span></li>
    <li>Cystic Fibrosis<span class="yn" style="left:178px"><span class="box"></span><b>Yes</b><span class="box"></span>No</span></li>
    <li>Emphysema<span class="yn" style="left:178px"><span class="box"></span><b>Yes</b><span class="box"></span>No</span></li>
    <li>Pneumonia<span class="yn" style="left:178px"><span class="box"></span><b>Yes</b><span class="box"></span>No</span></li>
  </ul>

  <div class="sec-head" style="left:27px;top:577px"><span>INFECTIOUS DISEASE</span></div>
  <ul class="checklist" style="left:28px;top:596px;width:250px">
    <li>Creutzfeldt-Jakob Disease<span class="yn" style="left:178px"><span class="box"></span><b>Yes</b><span class="box"></span>No</span></li>
    <li>Hepatitis A,B,C,D<span class="yn" style="left:178px"><span class="box"></span><b>Yes</b><span class="box"></span>No</span></li>
    <li>HIV/AIDS<span class="yn" style="left:178px"><span class="box"></span><b>Yes</b><span class="box"></span>No</span></li>
    <li>Influenza<span class="yn" style="left:178px"><span class="box"></span><b>Yes</b><span class="box"></span>No</span></li>
    <li>Shingles<span class="yn" style="left:178px"><span class="box"></span><b>Yes</b><span class="box"></span>No</span></li>
    <li>Tuberculosis<span class="yn" style="left:178px"><span class="box"></span><b>Yes</b><span class="box"></span>No</span></li>
  </ul>

  <div class="sec-head" style="left:276px;top:51px"><span>HEART</span></div>
  <ul class="checklist" style="left:286px;top:71px;width:250px">
    <li>Angina<span class="yn" style="left:178px"><span class="box"></span><b>Yes</b><span class="box"></span>No</span></li>
    <li>Atrial fibrillation<span class="yn" style="left:178px"><span class="box"></span><b>Yes</b><span class="box"></span>No</span></li>
    <li>Blood Pressure (high/low)<span class="yn" style="left:178px"><span class="box"></span><b>Yes</b><span class="box"></span>No</span></li>
    <li>Congenital heart disease<span class="yn" style="left:178px"><span class="box"></span><b>Yes</b><span class="box"></span>No</span></li>
    <li>Heart attack<span class="yn" style="left:178px"><span class="box"></span><b>Yes</b><span class="box"></span>No</span></li>
    <li>Heart murmur<span class="yn" style="left:178px"><span class="box"></span><b>Yes</b><span class="box"></span>No</span></li>
    <li>Heart surgery<span class="yn" style="left:178px"><span class="box"></span><b>Yes</b><span class="box"></span>No</span></li>
    <li>Heart valve replacement<span class="yn" style="left:178px"><span class="box"></span><b>Yes</b><span class="box"></span>No</span></li>
    <li>Infective endocarditis<span class="yn" style="left:178px"><span class="box"></span><b>Yes</b><span class="box"></span>No</span></li>
    <li>Rheumatic heart disease<span class="yn" style="left:178px"><span class="box"></span><b>Yes</b><span class="box"></span>No</span></li>
    <li>Pacemaker<span class="yn" style="left:178px"><span class="box"></span><b>Yes</b><span class="box"></span>No</span></li>
    <li>Stent<span class="yn" style="left:178px"><span class="box"></span><b>Yes</b><span class="box"></span>No</span></li>
  </ul>

  <div class="sec-head" style="left:276px;top:238px"><span>OTHER</span></div>
  <ul class="checklist" style="left:286px;top:257px;width:250px">
    <li>Anxiety/PTSD<span class="yn" style="left:178px"><span class="box"></span><b>Yes</b><span class="box"></span>No</span></li>
    <li>Arthritis<span class="yn" style="left:178px"><span class="box"></span><b>Yes</b><span class="box"></span>No</span></li>
    <li>Alzheimer's<span class="yn" style="left:178px"><span class="box"></span><b>Yes</b><span class="box"></span>No</span></li>
    <li>Asthma<span class="yn" style="left:178px"><span class="box"></span><b>Yes</b><span class="box"></span>No</span></li>
    <li>Anaphylaxis<span class="yn" style="left:178px"><span class="box"></span><b>Yes</b><span class="box"></span>No</span></li>
    <li>Auto-immune disease<span class="yn" style="left:178px"><span class="box"></span><b>Yes</b><span class="box"></span>No</span></li>
    <li>Coeliac<span class="yn" style="left:178px"><span class="box"></span><b>Yes</b><span class="box"></span>No</span></li>
    <li>Depression<span class="yn" style="left:178px"><span class="box"></span><b>Yes</b><span class="box"></span>No</span></li>
    <li>Diabetes<span class="yn" style="left:178px"><span class="box"></span><b>Yes</b><span class="box"></span>No</span></li>
    <li>Epilepsy<span class="yn" style="left:178px"><span class="box"></span><b>Yes</b><span class="box"></span>No</span></li>
    <li>Kidney disease<span class="yn" style="left:178px"><span class="box"></span><b>Yes</b><span class="box"></span>No</span></li>
    <li>Liver disease<span class="yn" style="left:178px"><span class="box"></span><b>Yes</b><span class="box"></span>No</span></li>
    <li>Osteoporosis<span class="yn" style="left:178px"><span class="box"></span><b>Yes</b><span class="box"></span>No</span></li>
    <li>Parkinson's<span class="yn" style="left:178px"><span class="box"></span><b>Yes</b><span class="box"></span>No</span></li>
    <li>Radiation to head/neck<span class="yn" style="left:178px"><span class="box"></span><b>Yes</b><span class="box"></span>No</span></li>
    <li>Schizophrenia<span class="yn" style="left:178px"><span class="box"></span><b>Yes</b><span class="box"></span>No</span></li>
    <li>Snoring<span class="yn" style="left:178px"><span class="box"></span><b>Yes</b><span class="box"></span>No</span></li>
    <li>Sleep apnea<span class="yn" style="left:178px"><span class="box"></span><b>Yes</b><span class="box"></span>No</span></li>
    <li>Stroke<span class="yn" style="left:178px"><span class="box"></span><b>Yes</b><span class="box"></span>No</span></li>
  </ul>

  <div class="field" style="left:286px;top:518px;width:236px">Other :<span class="line"></span></div>
  <div class="abs" style="left:318px;top:546px;width:204px;border-bottom:.8px solid var(--rule)"></div>
  <div class="abs" style="left:318px;top:566px;width:204px;border-bottom:.8px solid var(--rule)"></div>
  <div class="field" style="left:286px;top:605px;width:236px">Signature :<span class="line"></span></div>
  <div class="field" style="left:286px;top:631px;width:236px">Date :<span class="line"></span></div>

  <div class="brand" style="left:28px;top:698px;font-size:23px">harbour dental</div>
  <p class="thanks">Thank you for the time to complete your medical history form.<br>Oral health is linked overall health and this comprehensive questionnaire will help us to provide you with optimal ans safe care.</p>

  <footer class="foot">
    <div class="foot-phone"><svg width="10" height="10" viewBox="0 0 20 20"><circle cx="10" cy="10" r="8.6" fill="none" stroke="currentColor" stroke-width="1.6"/><path d="M7 5.5l1.6 2.4-1 1.2a6 6 0 0 0 3.3 3.3l1.2-1 2.4 1.6-.8 1.6c-3.8-.3-7.2-3.7-7.5-7.5z" fill="currentColor"/></svg>(02) 40 123 456</div>
    <div class="foot-addr"><svg width="7" height="10" viewBox="0 0 14 20"><path d="M7 0a7 7 0 0 0-7 7c0 5 7 13 7 13s7-8 7-13a7 7 0 0 0-7-7zm0 9.5A2.5 2.5 0 1 1 7 4.5a2.5 2.5 0 0 1 0 5z" fill="currentColor"/></svg>Harbour Dental, 3.04/118 Coastline Rd, Bayview NSW. 2260</div>
  </footer>
</section>

</body>
</html>
```